Lumo Organic Baby Wipes for retail sales into supermarkets

Design a new Organic Baby Wipes Pack that has a similar feel and details to the attachments under the Brand Name LUMO Organics. Please keep all writing in English and highlight the following info on the Pack. - 80 Pack, 100% Biodegradable,
Aloe Vera, Chamomile,Natural Vitamin E to soothe baby's skin.
Hypo Allergenic, pH Balanced for baby's skin.
Fragrance Free, Alcohol Free, Chlorine Free, Parabens Free.

Target Market(s)

Mums looking for a Organic Baby Wipe

Industry/Entity Type

Baby

Font styles to use
Sans Serif

Colors
9bcb3c
abd036
cadf82
ffffff

Requirements
Must have
• Lumo Organics, White Base, majority green writing with different shades, touches of Brown to represent Bamboo Wipes.
• Please make ORGANIC writing very big.
Nice to have
• Natural Organic feel going to use matt packaging.
Should not have
• Cluttered too much information

```html
<!DOCTYPE html>
<html lang="en">
<head>
<meta charset="utf-8">
<title>Lumo Organic Baby Wipes – Pack Front</title>
<link href="https://fonts.googleapis.com/css2?family=Arvo:wght@700&family=Oswald:wght@600&family=Pathway+Gothic+One&display=swap" rel="stylesheet">
<style>
  :root {
    --backdrop: #e9f6ee;
    --pack-white: #ffffff;
    --leaf: #9bcb3c;
    --lime: #abd036;
    --pale-lime: #cadf82;
    --deep-green: #4f7d2a;
    --mid-green: #6aa337;
    --bamboo-brown: #8a5524;
    --ink: #2f3a1e;
    --photo-light: #f3e6dc;
    --photo-warm: #c98c68;
    --photo-dark: #7a4a30;
  }
  * { margin: 0; padding: 0; box-sizing: border-box; }
  html, body { width: 1200px; height: 900px; overflow: hidden; }
  body { background: var(--backdrop); position: relative; }

  .pack {
    position: absolute; left: 150px; top: 210px;
    width: 900px; height: 470px;
    background: linear-gradient(180deg, #eef5d8 0%, var(--pack-white) 14%, var(--pack-white) 82%, #eef4dc 100%);
    overflow: hidden;
  }
  .crimp {
    position: absolute; top: 0; bottom: 0; width: 22px;
    background: repeating-linear-gradient(90deg, var(--pale-lime) 0 3px, #e4eec4 3px 6px);
  }
  .crimp--left { left: 0; }
  .crimp--right { right: 0; }

  .brand-name {
    position: absolute; left: 38px; top: 30px;
    font-family: 'Arvo', serif; font-weight: 700;
    font-size: 86px; line-height: 1; color: var(--mid-green);
  }
  .product-word {
    position: absolute; left: 30px; top: 140px;
    font-family: 'Oswald', sans-serif; font-weight: 600;
    font-size: 90px; line-height: 1; letter-spacing: 21px;
    color: var(--bamboo-brown);
  }
  .product-type {
    position: absolute; left: 156px; top: 228px;
    font-family: 'Arvo', serif; font-weight: 700;
    font-size: 40px; line-height: 1; color: var(--deep-green);
  }

  .benefits-band {
    position: absolute; left: 0; top: 304px; width: 330px; height: 128px;
    background: linear-gradient(90deg, var(--leaf) 0%, var(--lime) 55%, rgba(202,223,130,0) 100%);
    padding: 10px 0 0 30px;
  }
  .benefits {
    font-family: 'Pathway Gothic One', sans-serif;
    font-size: 19px; line-height: 23.5px; color: var(--ink);
  }

  .origin-seal { position: absolute; left: 318px; top: 330px; }
  .count-badge { position: absolute; left: 410px; top: 318px; width: 80px; text-align: center; }
  .count-label {
    font-family: 'Oswald', sans-serif; font-weight: 600;
    font-size: 15px; color: var(--deep-green); display: block; margin-bottom: 2px;
  }
  .hex {
    position: relative; width: 74px; height: 84px; margin: 0 auto;
    background: var(--leaf);
    clip-path: polygon(50% 0, 100% 25%, 100% 75%, 50% 100%, 0 75%, 0 25%);
    color: var(--pack-white); text-align: center;
    font-family: 'Oswald', sans-serif; font-weight: 600;
  }
  .hex-value { display: block; font-size: 24px; line-height: 1; padding-top: 22px; }
  .hex-text { display: block; font-size: 9px; line-height: 1.2; }

  .lifestyle-photo {
    position: absolute; left: 486px; top: 0; width: 392px; height: 368px;
    background:
      radial-gradient(ellipse at 70% 20%, var(--photo-dark) 0%, rgba(122,74,48,0) 45%),
      radial-gradient(ellipse at 40% 45%, var(--photo-light) 0%, #e8c7b0 40%, var(--photo-warm) 75%),
      var(--photo-light);
  }

  .tagline-band {
    position: absolute; left: 670px; top: 390px; width: 230px; height: 46px;
    background: linear-gradient(90deg, rgba(155,203,60,0) 0%, var(--leaf) 30%, var(--mid-green) 100%);
    font-family: 'Pathway Gothic One', sans-serif;
    font-size: 25px; line-height: 46px; color: var(--pack-white);
    text-align: right; padding-right: 30px;
  }
</style>
</head>
<body>
  <section class="pack">
    <div class="crimp crimp--left"></div>
    <div class="crimp crimp--right"></div>

    <div class="brand-name">Lumo</div>
    <h1 class="product-word">ORGANIC</h1>
    <h2 class="product-type">Baby Wipes</h2>

    <div class="benefits-band">
      <p class="benefits">
        Aloe Vera, Chamomile, Natural Vitamin E<br>
        to soothe baby's skin, Hypo Allergenic,<br>
        PH Balanced for baby's skin.<br>
        Fragrance Free, Alcohol Free,<br>
        Chlorine Free, Parabens Free.
      </p>
    </div>

    <svg class="origin-seal" width="80" height="64" viewBox="0 0 80 64" role="img" aria-label="Origin seal">
      <circle cx="40" cy="32" r="28" fill="none" stroke="var(--leaf)" stroke-width="3"/>
    </svg>

    <div class="count-badge">
      <span class="count-label">80 ★ Pack</span>
      <div class="hex">
        <span class="hex-value">100%</span>
        <span class="hex-text">Biodegradable</span>
      </div>
    </div>

    <div class="lifestyle-photo" role="img" aria-label="Photo of a smiling baby lying down, held close by its mother"></div>

    <div class="tagline-band">Because We Care</div>
  </section>
</body>
</html>
```